Velvet Lantern rebranding my business with a new business card

I have my new logo and now I need a refresher on my business cards. I really want something fun and fresh. I like black background or anything to make the color pop.
Logo
Name: Velvet Lantern
Contact Info as stated below:
Mira Pellow
555-013-4762
Logo
Name: Velvet Lantern
Mira Pellow
555-013-4762
fb.me/VelvetLanternbyMira
Instagram: @VelvetLanternbyMira

Industry/Entity Type

Business

Contact Information for Business Card

double-sided. Logo on one side. Contact info on the other.

Requirements
Must have
• Logo
• Name: Velvet Lantern
• Contact Info as stated below:
• Mira Pellow
• 555-013-4762
• fb.me/VelvetLanternbyMira
• fb.me/VelvetLanternbyMira

```html
<!DOCTYPE html>
<html lang="en">
<head>
<meta charset="utf-8">
<title>Velvet Lantern – Business Card</title>
<link href="https://fonts.googleapis.com/css2?family=Roboto+Slab:wght@400;500&family=Roboto:wght@400&display=swap" rel="stylesheet">
<style>
  :root {
    --backdrop: #ece8e3;
    --card-white: #ffffff;
    --blush: #f2a9bb;
    --blush-light: #f6bccb;
    --blush-line: #f7c7d3;
    --ink: #2a2a2a;
    --teal: #63cbbd;
    --teal-deep: #4fb8aa;
    --paper-edge: #d9d9d9;
  }
  * { box-sizing: border-box; margin: 0; padding: 0; }
  html, body { width: 1200px; height: 911px; overflow: hidden; background: var(--backdrop); }
  .stage {
    width: 1200px; height: 911px;
    display: flex; align-items: center; justify-content: center; gap: 60px;
  }
  .card {
    position: relative; width: 520px; height: 300px;
    border-radius: 22px; overflow: hidden;
    box-shadow: 0 6px 18px rgba(0,0,0,.18);
  }
  /* Contact side */
  .card--contact { background: var(--card-white); }
  .contact-disc {
    position: absolute; left: 205px; top: -95px;
    width: 470px; height: 470px; border-radius: 50%;
    background: linear-gradient(160deg, var(--blush-light), var(--blush));
    box-shadow: 0 0 0 6px var(--card-white), 0 0 0 8px var(--blush-line), 0 0 0 11px var(--card-white), 0 0 0 13px var(--ink);
  }
  .contact-block {
    position: absolute; left: 265px; top: 78px;
    color: var(--ink);
  }
  .contact-name {
    font-family: "Roboto Slab", serif; font-weight: 500;
    font-size: 27px; letter-spacing: .5px; text-transform: uppercase;
    margin-bottom: 18px;
  }
  .contact-list { list-style: none; font-family: "Roboto", sans-serif; font-size: 15px; }
  .contact-list li { display: flex; align-items: center; gap: 9px; margin-bottom: 7px; }
  .contact-list svg { width: 13px; height: 13px; flex: none; }
  .badge {
    position: absolute; left: 38px; top: 72px;
    width: 160px; height: 160px; border-radius: 50%;
    border: 2px solid var(--blush);
    box-shadow: inset 0 0 0 5px var(--card-white), inset 0 0 0 7px var(--blush-line);
    display: flex; align-items: center; justify-content: center;
  }
  .brand-name {
    font-family: "Roboto Slab", serif; font-weight: 500;
    color: var(--ink); text-align: center; line-height: 1.1;
  }
  .badge .brand-name { font-size: 20px; }
  /* Logo side */
  .card--logo { background: linear-gradient(150deg, var(--teal), var(--teal-deep)); }
  .card--logo .brand-name {
    position: absolute; left: 0; right: 0; top: 50%; transform: translateY(-50%);
    font-size: 38px; color: var(--card-white);
  }
  .web-vertical {
    position: absolute; left: 30px; top: 150px;
    transform: translate(-50%, -50%) rotate(90deg); transform-origin: center;
    font-family: "Roboto", sans-serif; font-size: 13px; letter-spacing: 6px;
    color: var(--card-white); white-space: nowrap;
  }
</style>
</head>
<body>
<main class="stage">
  <section class="card card--contact" aria-label="Contact side">
    <div class="contact-disc"></div>
    <div class="contact-block">
      <h1 class="contact-name">Mira Pellow</h1>
      <ul class="contact-list">
        <li><svg viewBox="0 0 24 24" aria-hidden="true"><path fill="#2a2a2a" d="M6.6 10.8a15 15 0 0 0 6.6 6.6l2.2-2.2a1 1 0 0 1 1-.25 11.4 11.4 0 0 0 3.6.6 1 1 0 0 1 1 1V20a1 1 0 0 1-1 1A17 17 0 0 1 3 4a1 1 0 0 1 1-1h3.5a1 1 0 0 1 1 1c0 1.25.2 2.45.6 3.6a1 1 0 0 1-.25 1z"/></svg>555-013-4762</li>
        <li><svg viewBox="0 0 24 24" aria-hidden="true"><circle cx="12" cy="12" r="10" fill="#2a2a2a"/><path d="M2 12h20M12 2c3 3 3 17 0 20M12 2c-3 3-3 17 0 20" stroke="#f2a9bb" stroke-width="1.5" fill="none"/></svg>www.velvetlantern.com</li>
        <li><svg viewBox="0 0 24 24" aria-hidden="true"><rect x="2" y="2" width="20" height="20" rx="3" fill="#2a2a2a"/></svg>fb.me/VelvetLanternbyMira</li>
      </ul>
    </div>
    <div class="badge"><span class="brand-name">Velvet<br>Lantern</span></div>
  </section>

  <section class="card card--logo" aria-label="Logo side">
    <span class="web-vertical">www.velvetlantern.com</span>
    <span class="brand-name">Velvet Lantern</span>
  </section>
</main>
</body>
</html>
```